Business Card for a Jewellery Brand

Business card for an upscale jewellery brand. Attached is the brand logo and icon and color board. I am looking for two card versions: one for the founder and one is generic. The card should be elegant and convey upscale and premium feel. I am open to both square and rectangle card shapes.

Industry/Entity Type

Jewelry

Contact Information for Business Card

Two cards: (1) Sunela Parvaniya (Founder) (2) General
(1) Sunela Parvaniya card should have Name: Sunela Parvaniya, Title: Founder Email id: sunela@quiremo.com.au. Phone no: +61452913307
(2) Generic card should have Email id: info@quiremo.com.au. Phone no: +61436207518

Requirements
Must have
• Workmark
• ICON
• Phone no
• Email ID
• ABN: 58219740312 (Note: ABN is Business number in Australia)
• Website: www.quiremo.com.au
• Instagram: quiremo_jewellery
• Facebook: @quiremojewellery
Nice to have
• Tagline

```html
<!DOCTYPE html>
<html lang="en">
<head>
<meta charset="utf-8">
<title>Quiremo Business Cards</title>
<link rel="stylesheet" href="https://fonts.googleapis.com/css2?family=Roboto:wght@400;500&display=swap">
<style>
  :root {
    --backdrop: #646569;
    --card: #1e2423;
    --rose: #dba69c;
    --ink-light: #f4f2f1;
    --card-w: 780px;
    --card-h: 440px;
  }
  * { margin: 0; padding: 0; box-sizing: border-box; }
  html, body { width: 1200px; height: 1200px; overflow: hidden; }
  body {
    background: var(--backdrop);
    font-family: "Roboto", Arial, sans-serif;
    display: flex;
    flex-direction: column;
    align-items: center;
    justify-content: center;
    gap: 44px;
  }
  .card {
    width: var(--card-w);
    height: var(--card-h);
    background: var(--card);
    position: relative;
    box-shadow: 0 6px 18px rgba(0,0,0,.25);
  }

  /* Front */
  .card-front {
    display: flex;
    flex-direction: column;
    align-items: center;
    justify-content: center;
    gap: 36px;
  }
  .brand-dot {
    display: block;
    width: 120px; height: 120px;
    border: 5px solid var(--rose);
    border-radius: 50%;
  }
  .wordmark {
    color: var(--rose);
    font-weight: 400;
    letter-spacing: .32em;
    text-transform: uppercase;
    white-space: nowrap;
  }
  .card-front .wordmark { font-size: 56px; margin-right: -.32em; }

  /* Back */
  .card-back .brand-dot {
    position: absolute;
    left: 112px; top: 112px;
    width: 140px; height: 140px;
  }
  .divider {
    position: absolute;
    left: 340px; top: 40px;
    width: 3px; height: 238px;
    background: var(--rose);
  }
  .contact {
    position: absolute;
    left: 370px; top: 30px;
    color: var(--ink-light);
  }
  .contact-name { font-size: 27px; font-weight: 400; }
  .contact-title { font-size: 20px; color: var(--rose); margin: 4px 0 10px; }
  .contact-list { list-style: none; font-size: 20px; line-height: 1.42; }
  .contact-list .label { color: var(--rose); margin-right: 6px; }
  .card-back .wordmark {
    position: absolute;
    left: 62px; bottom: 38px;
    font-size: 40px;
  }
  .address {
    position: absolute;
    left: 420px; bottom: 60px;
    color: var(--ink-light);
    font-size: 20px;
    line-height: 1.35;
    font-style: normal;
  }
</style>
</head>
<body>
  <section class="card card-front" aria-label="Card front">
    <span class="brand-dot" aria-hidden="true"></span>
    <span class="wordmark">Quiremo</span>
  </section>

  <section class="card card-back" aria-label="Card back, founder">
    <span class="brand-dot" aria-hidden="true"></span>
    <span class="divider" aria-hidden="true"></span>
    <div class="contact">
      <h1 class="contact-name">Sunela Parvaniya</h1>
      <p class="contact-title">Founder</p>
      <ul class="contact-list">
        <li><span class="label">P:</span>+61452913307</li>
        <li><span class="label">E:</span>sunela@quiremo.com.au</li>
        <li><span class="label">In:</span>quiremo_jewellery</li>
        <li><span class="label">Fb:</span>quiremojewellery</li>
        <li><span class="label">W:</span>www.quiremo.com.au</li>
        <li><span class="label">ABN:</span>58219740312</li>
      </ul>
    </div>
    <span class="wordmark">Quiremo</span>
    <address class="address">482 Larkin Street, Suite 1400<br>Easton, Maryland 21601</address>
  </section>
</body>
</html>
```